Stage Design Company Business Card

We are looking to step up up our business card design for our team.

We are a Full service Design and Consultation company for Stage and TV with an emphasis in Theatrical Lighting.

We like our materials to be clean and modern with solid colors free of patterns and gradients. Our brand consists of 4 primary colors Purple, Black, Grey, and White. Provided is our Word Mark as well as our Symbol Logo.

We would like our cards to leave an impression beyond the information, show our attention to design and detail, and make our marks an easily recognized feature (together or apart) for our clients.

We need a warm approachable comfortable feel for some clients, and a professional flair for the board member type clients.

Attached are our brand elements, and our existing cards to give a sense of our style and a glipse at the information we provide on our cards.

Target Market(s)

broad client base from church leaders to high school teachers and architects.

Industry/Entity Type

Business

Contact Information for Business Card

We format our phone number with periods not parenthesis or dashes. Information will be edited for each of our team members, and team member specific cards are not part of this scope, but rather a template so to speak.

Font styles to use
Sans Serif

Colors
6b449b
ffffff
000000
333333
aaaaaa

Requirements
Must have
• Wordmark and logo mark present (does not need to exist on the same side of card)
• Brand Colors,
• Name, Phone, Email, Address.
• Unique choices that make someone stop and take a second look
Nice to have
• It would be nice to somehow convey what we DO, as our brand name does not lend itself to this, outside of an obvious tagline though.....
• social media if not crowded. all of our handles match (instagram, twitter, facebook)
Should not have
• "clipart"

```html
<!DOCTYPE html>
<html lang="en">
<head>
<meta charset="utf-8">
<title>Lumen Stageworks – Business Card</title>
<link href="https://fonts.googleapis.com/css2?family=Roboto+Condensed:wght@400&display=swap" rel="stylesheet">
<style>
  :root{
    --backdrop:#5f5f5f;
    --purple:#33006b;
    --ink:#111111;
    --ink-band:#111820;
    --grey:#777777;
    --rule:#cccccc;
    --paper:#ffffff;
  }
  *{box-sizing:border-box;margin:0;padding:0}
  html,body{width:1200px;height:1200px;overflow:hidden}
  body{
    background:var(--backdrop);
    font-family:"Roboto Condensed",Arial Narrow,sans-serif;
    position:relative;
  }
  .card{
    position:absolute;
    top:447px;
    width:540px;height:305px;
    overflow:hidden;
  }
  .card--front{left:40px;background:var(--paper);color:var(--ink)}
  .card--back{left:620px;background:var(--purple);color:var(--paper)}

  .person{position:absolute;left:43px;top:38px}
  .person__name{font-size:25px;line-height:1.1;letter-spacing:-0.2px}
  .person__title{font-size:13px;color:var(--grey);margin-top:1px}

  .wordmark{
    position:absolute;
    text-align:left;
    font-weight:400;
    text-transform:uppercase;
  }
  .card--front .wordmark{right:45px;top:38px;color:var(--ink)}
  .wordmark__main{display:block;font-size:28px;letter-spacing:20px;line-height:1}
  .wordmark__sub{display:block;font-size:8.5px;letter-spacing:10.3px;margin-top:10px}
  .card--front .wordmark__sub{color:var(--grey)}

  .rule{position:absolute;left:43px;right:46px;top:163px;border-top:1px solid var(--rule)}

  .contacts{position:absolute;left:43px;top:184px;list-style:none;font-size:17px;line-height:21px}
  .contacts li{display:flex;align-items:center;gap:8px}
  .contacts svg{width:12px;height:12px;fill:var(--purple);flex:none}

  .office{position:absolute;left:247px;top:185px;font-size:17px;line-height:21px}
  .office__name{color:var(--purple);font-size:15px}

  .band{position:absolute;bottom:0;height:23px}
  .band--dark{left:0;width:199px;background:var(--ink-band)}
  .band--purple{left:202px;right:0;background:var(--purple)}

  .card--back .brand{
    position:absolute;left:62px;top:100px;
    display:flex;align-items:center;gap:26px;
  }
  .brand__dot{width:60px;height:60px;border-radius:50%;background:var(--paper);flex:none}
  .card--back .wordmark{position:static}
  .card--back .wordmark__main{font-size:36px;letter-spacing:30px}
  .card--back .wordmark__sub{font-size:11px;letter-spacing:14.6px;margin-top:14px}
</style>
</head>
<body>

<section class="card card--front" aria-label="Business card front">
  <div class="person">
    <p class="person__name">Mara L Quinn</p>
    <p class="person__title">Job Title</p>
  </div>

  <div class="wordmark">
    <span class="wordmark__main">Lumen</span>
    <span class="wordmark__sub">Stageworks</span>
  </div>

  <div class="rule"></div>

  <ul class="contacts">
    <li><svg viewBox="0 0 12 12" aria-hidden="true"><path d="M3 0h6a1 1 0 0 1 1 1v10a1 1 0 0 1-1 1H3a1 1 0 0 1-1-1V1a1 1 0 0 1 1-1zm.5 1.5v8h5v-8z"/></svg>000.000.0000</li>
    <li><svg viewBox="0 0 12 12" aria-hidden="true"><path d="M2.5 0.5l2 2.5-1.2 1.3c.7 1.6 2 2.9 3.6 3.6L8.2 6.7l2.5 2-1.4 2.6C5 11 1 7 .5 2.2z"/></svg>555.214.7390</li>
    <li><svg viewBox="0 0 12 12" aria-hidden="true"><path d="M0 2.5h12v7H0zM1 3.3l5 3.3 5-3.3v-.1H1z"/></svg>mara@lumen-s.com</li>
    <li><svg viewBox="0 0 12 12" aria-hidden="true"><path d="M6 0a6 6 0 1 0 0 12A6 6 0 0 0 6 0zm0 1c.8.8 1.3 2.3 1.4 4.5H4.6C4.7 3.3 5.2 1.8 6 1zM1.1 5.5h2.5c.1-1.7.4-3 .9-4A5 5 0 0 0 1.1 5.5zm7.3 0h2.5a5 5 0 0 0-3.4-4c.5 1 .8 2.3.9 4zm-7.3 1a5 5 0 0 0 3.4 4c-.5-1-.8-2.3-.9-4zm3.5 0c.1 2.2.6 3.7 1.4 4.5.8-.8 1.3-2.3 1.4-4.5zm3.8 0c-.1 1.7-.4 3-.9 4a5 5 0 0 0 3.4-4z"/></svg>lumen-s.com</li>
  </ul>

  <address class="office" style="font-style:normal">
    <p class="office__name">Lumen Stageworks</p>
    <p>18 N Harbor Ave</p>
    <p>Ridgefield, CO 80512</p>
  </address>

  <div class="band band--dark"></div>
  <div class="band band--purple"></div>
</section>

<section class="card card--back" aria-label="Business card back">
  <div class="brand">
    <span class="brand__dot" aria-hidden="true"></span>
    <div class="wordmark">
      <span class="wordmark__main">Lumen</span>
      <span class="wordmark__sub">Stageworks</span>
    </div>
  </div>
</section>

</body>
</html>
```